Pharmacy ad

need 2 pharmacy ads for the phone book. one for Brookvale Pharmacy and one for Cedarline Care Pharmacy. Dimensions for ad is 4.75in x 4.667 in. please see attached examples of ad uploaded as well logos of each pharmacy

```html
<!DOCTYPE html>
<html lang="en">
<head>
<meta charset="utf-8">
<title>Pharmacy Directory Ads</title>
<link href="https://fonts.googleapis.com/css2?family=Montserrat:wght@500;600;700;800&family=Oswald:wght@500&family=Lato:wght@400;700&display=swap" rel="stylesheet">
<style>
:root{
  --navy:#1f1a4a;
  --green:#6cbf3f;
  --green-dark:#4f9a2a;
  --yellow:#f6d31c;
  --blue:#3d4ea6;
  --strip:#f1f1f1;
  --ink:#2a2a2a;
  --white:#ffffff;
}
*{margin:0;padding:0;box-sizing:border-box}
html,body{width:1200px;height:903px;overflow:hidden;background:var(--white)}
body{position:relative;font-family:"Lato",sans-serif;color:var(--ink)}
.ad{position:absolute;top:194px;width:524px;height:515px;background:var(--white);overflow:hidden;box-shadow:0 2px 6px rgba(0,0,0,.3)}
.ad--brookvale{left:56px}
.ad--cedarline{left:621px}
.ad__shapes{position:absolute;inset:0}
.abs{position:absolute}
.brand{font-family:"Montserrat",sans-serif;font-weight:800;color:var(--navy);display:flex;align-items:center;gap:8px}
.brand__dot{width:18px;height:18px;border-radius:50%;background:var(--green);flex:none}
.tagline-small{font-family:"Lato",sans-serif;font-size:8px;color:var(--green-dark)}
.accept{display:flex;align-items:center;gap:11px;font-family:"Montserrat",sans-serif;font-size:9.5px;font-weight:600;color:var(--navy);white-space:nowrap}
.accept__label{font-weight:600;letter-spacing:.3px}
.accept__name{font-weight:700}
.offer{display:flex;align-items:center;gap:7px;color:var(--white)}
.offer__pct{font-family:"Oswald",sans-serif;font-weight:500;font-size:33px;line-height:1;color:var(--yellow)}
.ad--cedarline .offer__pct{color:var(--white)}
.offer__kind{font-family:"Montserrat",sans-serif;font-weight:600;font-size:12.5px;line-height:1}
.ad--cedarline .offer__kind{color:var(--yellow)}
.offer__word{font-family:"Montserrat",sans-serif;font-weight:600;font-size:19px;line-height:1;color:var(--green)}
.ad--cedarline .offer__word{color:var(--yellow)}
.offer__note{font-family:"Montserrat",sans-serif;font-weight:600;font-size:11px;color:var(--white);letter-spacing:.3px}
.services{list-style:none;font-family:"Lato",sans-serif;font-size:13.6px;color:var(--ink)}
.services li{position:relative;padding-left:20px}
.services li::before{content:"";position:absolute;left:0;top:5px;border-left:10px solid var(--navy);border-top:4px solid transparent;border-bottom:4px solid transparent}
.ad--brookvale .services li{height:21.5px}
.ad--cedarline .services li{margin-bottom:10px;line-height:16.5px;width:212px}
.hours{font-family:"Lato",sans-serif;font-weight:700;font-size:12px;color:var(--white);line-height:18.5px}
.motto{font-family:"Montserrat",sans-serif;font-weight:700;font-size:13.6px;letter-spacing:.4px;color:var(--navy)}
.ad--cedarline .motto{color:var(--blue)}
.contact{font-family:"Montserrat",sans-serif;color:var(--white);font-size:10.5px;line-height:13px}
.contact__row{display:flex;align-items:flex-start;gap:10px}
.contact__row svg{flex:none;margin-top:1px}
.contact__phone{font-weight:600;font-size:12.5px}
.visit{font-family:"Montserrat",sans-serif;font-size:12px;color:var(--yellow);display:flex;align-items:center;gap:5px}
.ad--cedarline .visit{color:var(--green)}
.visit__sq{width:10px;height:10px;background:currentColor}
</style>
</head>
<body>

<section class="ad ad--brookvale">
  <svg class="ad__shapes" width="524" height="515" viewBox="0 0 524 515">
    <defs>
      <linearGradient id="photoA" x1="0" y1="0" x2="1" y2="1">
        <stop offset="0" stop-color="#dfe6ec"/>
        <stop offset=".5" stop-color="#c9d3c8"/>
        <stop offset="1" stop-color="#e8e2dc"/>
      </linearGradient>
    </defs>
    <rect x="192" y="16" width="332" height="40" fill="var(--strip)"/>
    <polygon points="198,56 524,56 524,375 252,375" fill="url(#photoA)" role="img" aria-label="Photo of a pharmacist in a white coat standing with arms crossed before pharmacy shelves"/>
    <polygon points="0,146 220,146 212,203 0,203" fill="var(--navy)"/>
    <polygon points="0,206 232,206 224,264 0,264" fill="var(--navy)"/>
    <polygon points="254,375 524,375 524,403 258,403" fill="var(--green)"/>
    <polygon points="260,403 524,403 524,515 276,515" fill="var(--navy)"/>
    <polygon points="0,446 265,446 276,515 0,515" fill="var(--green)"/>
  </svg>

  <div class="abs" style="left:28px;top:62px;width:210px">
    <div class="brand" style="font-size:17px"><span class="brand__dot"></span>Brookvale Pharmacy</div>
    <div class="tagline-small" style="margin-top:6px;padding-left:26px">We Care About Your Health</div>
  </div>

  <div class="abs accept" style="left:206px;top:30px">
    <span class="accept__label">WE ACCEPT</span>
    <span class="accept__name">CardOne</span>
    <span class="accept__name">PayLink</span>
    <span class="accept__name">Harbour Life</span>
    <span class="accept__name">Isle Cover</span>
  </div>

  <div class="abs" style="left:18px;top:150px">
    <div class="offer"><span class="offer__pct">10 %</span><span><span class="offer__kind">SENIOR CITIZEN</span><br><span class="offer__word">DISCOUNT</span></span></div>
    <div class="offer__note">For patients 60 years &amp; over</div>
  </div>
  <div class="abs" style="left:18px;top:210px">
    <div class="offer"><span class="offer__pct">10 %</span><span><span class="offer__kind">STUDENT</span><br><span class="offer__word">DISCOUNT</span></span></div>
    <div class="offer__note" style="padding-left:2px">With valid ID card</div>
  </div>

  <ul class="abs services" style="left:20px;top:271px">
    <li>Certified Pharmacists</li>
    <li>Affordable prices</li>
    <li>Brand &amp; Generic Medicines</li>
    <li>Blood Pressure &amp; Glucose checks</li>
    <li>Personal care &amp; Beauty Products</li>
    <li>Injectables</li>
    <li>Special Orders</li>
    <li>Delivery service</li>
  </ul>

  <div class="abs hours" style="left:18px;top:454px">
    Monday – Friday 10am- 6pm<br>Saturday 10am-5pm<br>Sunday 10am-2pm (Maple Street branch)
  </div>

  <div class="abs motto" style="left:277px;top:382px">WE CARE ABOUT YOUR HEALTH</div>

  <div class="abs visit" style="left:422px;top:413px">Visit us on <span class="visit__sq"></span></div>

  <div class="abs contact" style="left:280px;top:426px">
    <div class="contact__row"><svg width="12" height="12" viewBox="0 0 12 12"><path d="M2 1l2 0 1 3-1.5 1a7 7 0 0 0 3 3L8 7l3 1v2a1 1 0 0 1-1 1A9 9 0 0 1 1 2a1 1 0 0 1 1-1z" fill="var(--yellow)"/></svg><span class="contact__phone">555-0174</span></div>
    <div class="contact__row" style="margin-top:2px"><svg width="12" height="14" viewBox="0 0 12 14"><path d="M6 1a4 4 0 0 1 4 4c0 3-4 8-4 8S2 8 2 5a4 4 0 0 1 4-4z" fill="none" stroke="var(--yellow)" stroke-width="1.6"/><circle cx="6" cy="5" r="1.4" fill="var(--yellow)"/></svg><span>19 Maple Street, Eastport<br>(opposite Grace Chapel)</span></div>
    <div class="contact__row" style="margin-top:6px;padding-left:6px"><svg width="12" height="12" viewBox="0 0 12 12"><path d="M2 1l2 0 1 3-1.5 1a7 7 0 0 0 3 3L8 7l3 1v2a1 1 0 0 1-1 1A9 9 0 0 1 1 2a1 1 0 0 1 1-1z" fill="var(--yellow)"/></svg><span class="contact__phone">555-0177</span></div>
    <div class="contact__row" style="margin-top:3px;padding-left:6px"><svg width="12" height="14" viewBox="0 0 12 14"><path d="M6 1a4 4 0 0 1 4 4c0 3-4 8-4 8S2 8 2 5a4 4 0 0 1 4-4z" fill="none" stroke="var(--yellow)" stroke-width="1.6"/><circle cx="6" cy="5" r="1.4" fill="var(--yellow)"/></svg><span>Harbour Quay, Food Court, Eastport</span></div>
  </div>
</section>

<section class="ad ad--cedarline">
  <svg class="ad__shapes" width="524" height="515" viewBox="0 0 524 515">
    <defs>
      <linearGradient id="photoB" x1="0" y1="0" x2="1" y2="1">
        <stop offset="0" stop-color="#e4e8ee"/>
        <stop offset=".5" stop-color="#d3cfc6"/>
        <stop offset="1" stop-color="#ebe4dc"/>
      </linearGradient>
    </defs>
    <rect x="223" y="20" width="301" height="58" fill="var(--strip)"/>
    <line x1="218" y1="20" x2="231" y2="76" stroke="var(--green)" stroke-width="2"/>
    <polygon points="211,78 524,78 524,406 260,406" fill="url(#photoB)" role="img" aria-label="Photo of a pharmacist in a white coat reading a medicine bottle beside pharmacy shelves"/>
    <polygon points="0,79 215,79 218,136 0,136" fill="var(--blue)"/>
    <polygon points="0,140 220,140 227,198 0,198" fill="var(--blue)"/>
    <polygon points="267,406 524,406 524,434 267,434" fill="var(--green)"/>
    <polygon points="271,434 524,434 524,515 284,515" fill="var(--blue)"/>
    <polygon points="0,458 272,458 280,515 0,515" fill="var(--green)"/>
  </svg>

  <div class="abs" style="left:20px;top:36px;width:200px">
    <div class="brand" style="font-size:15px;color:var(--blue)"><span class="brand__dot"></span>Cedarline Care Pharmacy</div>
  </div>

  <div class="abs accept" style="left:236px;top:45px;gap:8px;font-size:9px">
    <span class="accept__label">WE ACCEPT</span>
    <span class="accept__name">CardOne</span>
    <span class="accept__name">PayLink</span>
    <span class="accept__name">Harbour Life</span>
    <span class="accept__name">Isle Cover</span>
  </div>

  <div class="abs" style="left:12px;top:93px">
    <div class="offer"><span class="offer__pct">10 %</span><span><span class="offer__kind">SENIOR CITIZEN</span><br><span class="offer__word">DISCOUNT</span></span></div>
  </div>
  <div class="abs" style="left:12px;top:145px">
    <div class="offer"><span class="offer__pct">10 %</span><span><span class="offer__kind">STUDENT</span><br><span class="offer__word">DISCOUNT</span></span></div>
    <div class="offer__note" style="margin-top:-2px">With valid ID card</div>
  </div>

  <ul class="abs services" style="left:20px;top:208px">
    <li>Certified Pharmacists</li>
    <li>Affordable prices</li>
    <li>Brand and Generic Medicines</li>
    <li>Blood Pressure and Glucose checks</li>
    <li>Personal care and Beauty Products</li>
    <li>Injectables</li>
    <li>Special Orders</li>
    <li>Delivery service</li>
  </ul>

  <div class="abs hours" style="left:20px;top:463px">
    Monday – Saturday Thursday 8am- 7pm<br>Sunday 10am-2pm
  </div>

  <div class="abs motto" style="left:283px;top:413px">WHERE GOOD HEALTH BEGINS</div>

  <div class="abs visit" style="left:432px;top:443px">Visit us on <span class="visit__sq"></span></div>

  <div class="abs contact" style="left:289px;top:456px;font-size:12px;line-height:14.5px">
    <div class="contact__row"><svg width="12" height="12" viewBox="0 0 12 12"><path d="M2 1l2 0 1 3-1.5 1a7 7 0 0 0 3 3L8 7l3 1v2a1 1 0 0 1-1 1A9 9 0 0 1 1 2a1 1 0 0 1 1-1z" fill="var(--green)"/></svg><span class="contact__phone">555-0155</span></div>
    <div class="contact__row" style="margin-top:4px"><svg width="12" height="14" viewBox="0 0 12 14"><path d="M6 1a4 4 0 0 1 4 4c0 3-4 8-4 8S2 8 2 5a4 4 0 0 1 4-4z" fill="none" stroke="var(--green)" stroke-width="1.6"/><circle cx="6" cy="5" r="1.4" fill="var(--green)"/></svg><span>Unit C1, Seaview Hotel,<br>Harbor Road, Eastport</span></div>
  </div>
</section>

</body>
</html>
```